New design for www.TrimTable.com

On TrimTable you can find & book your hairdresser. TrimTable is the biggest platform in the Netherlands.

- The design should be a responcive design
- Should be able to go global, should fit in perfectly between all the big booking platforms like stayvo, ridlo etc,
- Should have te result of more bookings. :)
- We are ‘only’ asking a beautiful design, not a technical solution.
- We need a homepage (https://trimtable.com/), search resultpage ((https://trimtable.com/kapper/amsterdam/#), salonpage (https://trimtable.com/kapper/vorden/lumo-for-hair/), about us page (https://trimtable.com/aboutus/), for the hairdresser info page (https://trimtable.com/kapper/), login/register page (https://trimtable.com/account/signin/).

- On the page of the hairdresser there is a dynamic part. The part where you create your appointment. Please take a look at this part too after you choose your treatment (behandeling), employee (medewerker), Date (datum) and time (tijd). The part that you see after this, is the part where you fill in your data as a consumer.

I've added more logo's but mostly we use the green color.

A few of our competitors: www.plumsalo.com, www.korifex.com

Target Market(s)

All consumers

Industry/Entity Type

Hair And Beauty

Number of Pages Required

5+ page

Font styles to use
Sans Serif

Colors
abd036
c3c3c3
757575

Requirements
Must have
• Responsive
• We did an A/B test with the homepage. It turns out that option B works better then option A (take a look at the uploaded pictures). So what we need on the homepage: The USP's with the green checkboxes, The search button needs to by dynamic (changes for example from light green to dark green so you can see you can click it) The call to action sentence Zoek & Vind je kapsalon, the searchfield and searchbutton should be seperated.
Nice to have
• The style that we like is the flat design style. The website should be simple, clean and it should feel a bit like a luxury thing. Because an appointment with the hairdresser can be a real treat and luxury moment for yourself.
• The luxury feeling and flat design that is in the www.ridlo.com website is really nice for example. But then it has to be a bit more light and not so black and dark.

```html
<!DOCTYPE html>
<html lang="en">
<head>
<meta charset="utf-8">
<title>TrimTable – Find &amp; book your hairdresser</title>
<link href="https://fonts.googleapis.com/css2?family=Roboto:wght@300;400;500;700&display=swap" rel="stylesheet">
<style>
  :root {
    --green: #abd036;
    --green-dark: #8fb322;
    --green-band: #9cc23a;
    --grey-light: #c3c3c3;
    --grey: #757575;
    --ink: #333333;
    --paper: #ffffff;
    --mist: #f4f4f4;
    --night: #1f1f1f;
  }
  * { box-sizing: border-box; margin: 0; padding: 0; }
  html, body { width: 1200px; height: 2472px; overflow: hidden; }
  body { font-family: 'Roboto', Arial, sans-serif; color: var(--ink); background: var(--paper); position: relative; }

  /* Hero */
  .hero { position: absolute; top: 0; left: 0; width: 1200px; height: 660px; }
  .hero-photo { position: absolute; inset: 0; background: linear-gradient(100deg, #5a5d60 0%, #8a8a86 40%, #b9a894 70%, #6e5a48 100%); }
  .topbar { position: absolute; top: 44px; left: 70px; right: 70px; display: flex; justify-content: space-between; align-items: center; color: var(--paper); }
  .brand { display: flex; align-items: center; gap: 12px; font-size: 30px; font-weight: 500; color: var(--paper); }
  .brand-dot { width: 28px; height: 28px; border-radius: 50%; background: var(--paper); }
  .account { font-size: 17px; display: flex; gap: 18px; }
  .hero-panel { position: absolute; left: 220px; top: 285px; width: 760px; height: 300px; background: rgba(20,20,20,.45); }
  .hero-title { position: absolute; top: 312px; left: 0; width: 1200px; text-align: center; color: var(--paper); font-size: 30px; font-weight: 400; line-height: 40px; }
  .search { position: absolute; top: 432px; left: 290px; width: 620px; height: 60px; display: flex; }
  .search-field { flex: 1; background: var(--paper); display: flex; align-items: center; padding-left: 22px; font-size: 17px; color: var(--grey); }
  .search-select { width: 120px; background: var(--paper); border-left: 1px solid var(--grey-light); display: flex; align-items: center; justify-content: center; font-size: 14px; color: var(--grey); }
  .search-button { width: 120px; margin-left: 6px; background: var(--green); color: var(--paper); font-size: 20px; display: flex; align-items: center; justify-content: center; }
  .hero-alt { position: absolute; top: 518px; left: 0; width: 1200px; text-align: center; color: var(--paper); font-size: 26px; font-weight: 300; }
  .hero-alt span { margin: 0 18px; }
  .dots { position: absolute; top: 628px; left: 0; width: 1200px; display: flex; justify-content: center; gap: 10px; }
  .dots i { width: 11px; height: 11px; border-radius: 50%; background: var(--paper); opacity: .6; }
  .dots i:first-child { opacity: 1; }

  /* How it works */
  .how { position: absolute; top: 660px; left: 0; width: 1200px; height: 440px; background: var(--mist); }
  .section-title { text-align: center; font-weight: 400; }
  .how .section-title { margin-top: 56px; color: var(--green); font-size: 34px; }
  .steps { position: absolute; top: 140px; left: 0; width: 1200px; }
  .step { position: absolute; width: 320px; text-align: center; }
  .step-ring { width: 196px; height: 196px; margin: 0 auto; border-radius: 50%; border: 2px solid var(--grey-light); background: var(--paper); display: flex; align-items: center; justify-content: center; }
  .step-art { width: 120px; height: 120px; border-radius: 50%; background: linear-gradient(#eef3df, #dfe8c4); }
  .step-label { margin-top: 22px; font-size: 18px; line-height: 24px; color: var(--ink); }

  /* App band */
  .app { position: absolute; top: 1100px; left: 0; width: 1200px; height: 460px; background: var(--green-band); }
  .phone { position: absolute; left: 160px; top: 40px; width: 220px; height: 420px; border-radius: 34px; background: linear-gradient(#f5f5f5, #dcdcdc); }
  .phone-screen { position: absolute; left: 14px; top: 60px; width: 192px; height: 300px; background: #111; display: flex; flex-direction: column; align-items: center; justify-content: center; gap: 16px; }
  .phone-screen .brand-dot { width: 70px; height: 70px; background: var(--green); }
  .phone-screen .brand { font-size: 22px; }
  .app-copy { position: absolute; left: 490px; top: 80px; width: 620px; color: var(--paper); }
  .app-copy h2 { font-size: 32px; font-weight: 400; line-height: 40px; }
  .app-copy h3 { font-size: 25px; font-weight: 300; line-height: 32px; margin-top: 6px; }
  .app-copy p { margin-top: 18px; font-size: 14px; line-height: 22px; opacity: .9; }
  .app-button { display: inline-block; margin-top: 26px; padding: 14px 28px; background: var(--paper); color: var(--ink); font-size: 16px; border-radius: 3px; }

  /* Stats */
  .stats { position: absolute; top: 1560px; left: 0; width: 1200px; height: 430px; background: var(--paper); }
  .stats .section-title { margin-top: 72px; font-size: 19px; font-weight: 500; color: var(--ink); }
  .stat { position: absolute; top: 168px; width: 200px; text-align: center; }
  .stat svg { display: block; margin: 0 auto; }
  .stat-label { margin-top: 26px; font-size: 16px; color: var(--ink); }

  /* Subscribe */
  .subscribe { position: absolute; top: 1990px; left: 0; width: 1200px; height: 190px; }
  .subscribe-photo { position: absolute; inset: 0; background: linear-gradient(90deg, #eeeeee 0%, #e6e4e0 55%, #d8cfc6 80%, #c9bcaf 100%); }
  .subscribe h2 { position: absolute; top: 34px; width: 1200px; text-align: center; font-size: 24px; font-weight: 400; color: var(--green); }
  .subscribe-form { position: absolute; top: 84px; left: 400px; width: 400px; height: 52px; display: flex; border: 1px solid var(--grey-light); background: var(--paper); }
  .subscribe-form span { flex: 1; display: flex; align-items: center; padding-left: 18px; font-size: 15px; color: var(--grey); }
  .subscribe-form b { width: 60px; border-left: 1px solid var(--grey-light); display: flex; align-items: center; justify-content: center; }

  /* Footer */
  .footer { position: absolute; top: 2180px; left: 0; width: 1200px; height: 220px; background: var(--green-band); color: var(--paper); }
  .footer-col { position: absolute; top: 30px; font-size: 12px; line-height: 20px; }
  .footer-col h4 { font-size: 14px; font-weight: 500; margin-bottom: 12px; letter-spacing: .5px; }
  .footer-col ul { list-style: none; }
  .news-form { display: flex; margin-top: 10px; height: 32px; width: 240px; }
  .news-form span { flex: 1; background: var(--paper); color: var(--grey); padding-left: 10px; display: flex; align-items: center; }
  .news-form b { width: 70px; background: var(--night); display: flex; align-items: center; justify-content: center; font-weight: 400; }
  .socials { display: flex; gap: 14px; margin-top: 22px; margin-left: 40px; }
  .socials i { width: 30px; height: 30px; border-radius: 50%; background: rgba(255,255,255,.35); }
  .copyright { position: absolute; top: 2400px; left: 0; width: 1200px; height: 72px; background: var(--night); color: var(--grey-light); font-size: 13px; display: flex; align-items: center; justify-content: center; }
</style>
</head>
<body>

<header class="hero">
  <div class="hero-photo" role="img" aria-label="Photo of a smiling woman with long hair in a hair salon"></div>
  <div class="topbar">
    <div class="brand"><span class="brand-dot"></span>TrimTable</div>
    <nav class="account"><span>Login</span><span>|</span><span>Register</span></nav>
  </div>
  <div class="hero-panel"></div>
  <h1 class="hero-title">The greatest hairdresser bookings site in the<br>Netherlands with 541 hairdressers.</h1>
  <div class="search">
    <div class="search-field">Zoek op plaats of postcode</div>
    <div class="search-select">Alle diensten ▾</div>
    <div class="search-button">Search</div>
  </div>
  <p class="hero-alt">or search salon name<span>|</span>Map</p>
  <div class="dots"><i></i><i></i><i></i><i></i><i></i></div>
</header>

<section class="how">
  <h2 class="section-title">How does it work?</h2>
  <div class="steps">
    <div class="step" style="left:80px">
      <div class="step-ring"><div class="step-art" role="img" aria-label="Illustration of map pins and a magnifier"></div></div>
      <p class="step-label">Search &amp; Find Hairdresser</p>
    </div>
    <div class="step" style="left:440px">
      <div class="step-ring"><div class="step-art" role="img" aria-label="Illustration of a hand holding a phone"></div></div>
      <p class="step-label">Book your appointment<br>online with 100% certainty</p>
    </div>
    <div class="step" style="left:800px">
      <div class="step-ring"><div class="step-art" role="img" aria-label="Illustration of a woman with a new hairstyle"></div></div>
      <p class="step-label">Enjoy your new hairstyle</p>
    </div>
  </div>
</section>

<section class="app">
  <div class="phone" role="img" aria-label="Smartphone showing the TrimTable app">
    <div class="phone-screen"><span class="brand-dot"></span><span class="brand">TrimTable</span></div>
  </div>
  <div class="app-copy">
    <h2>All the hairdressers of Netherlands in your pocket?</h2>
    <h3>Download the Android APP and always feel<br>a place to make a good hairstyle</h3>
    <p>Find a salon near you, compare treatments and prices, read honest reviews from other guests and book your appointment in seconds. Your bookings are saved in the app, so you always know when your next moment of luxury is planned and can change it whenever you like.</p>
    <span class="app-button">Download Android App</span>
  </div>
</section>

<section class="stats">
  <h2 class="section-title">Last appointment on October 15, 2015 at 17:07</h2>
  <div class="stat" style="left:68px">
    <svg width="150" height="150" viewBox="0 0 150 150"><circle cx="75" cy="75" r="66" fill="none" stroke="#e6e6e6" stroke-width="9"/><circle cx="75" cy="75" r="66" fill="none" stroke="#abd036" stroke-width="9" stroke-dasharray="300 415" transform="rotate(-90 75 75)"/><text x="75" y="82" text-anchor="middle" font-family="Roboto, sans-serif" font-size="20" fill="#333">541</text></svg>
    <p class="stat-label">salons</p>
  </div>
  <div class="stat" style="left:288px">
    <svg width="150" height="150" viewBox="0 0 150 150"><circle cx="75" cy="75" r="66" fill="none" stroke="#e6e6e6" stroke-width="9"/><circle cx="75" cy="75" r="66" fill="none" stroke="#abd036" stroke-width="9" stroke-dasharray="250 415" transform="rotate(-90 75 75)"/><text x="75" y="82" text-anchor="middle" font-family="Roboto, sans-serif" font-size="20" fill="#333">16 413</text></svg>
    <p class="stat-label">Treatments for booking</p>
  </div>
  <div class="stat" style="left:508px">
    <svg width="150" height="150" viewBox="0 0 150 150"><circle cx="75" cy="75" r="66" fill="none" stroke="#e6e6e6" stroke-width="9"/><circle cx="75" cy="75" r="66" fill="none" stroke="#abd036" stroke-width="9" stroke-dasharray="340 415" transform="rotate(-90 75 75)"/><text x="75" y="82" text-anchor="middle" font-family="Roboto, sans-serif" font-size="20" fill="#333">579848</text></svg>
    <p class="stat-label">Agreements</p>
  </div>
  <div class="stat" style="left:728px">
    <svg width="150" height="150" viewBox="0 0 150 150"><circle cx="75" cy="75" r="66" fill="none" stroke="#e6e6e6" stroke-width="9"/><circle cx="75" cy="75" r="66" fill="none" stroke="#abd036" stroke-width="9" stroke-dasharray="200 415" transform="rotate(-90 75 75)"/><text x="75" y="82" text-anchor="middle" font-family="Roboto, sans-serif" font-size="20" fill="#333">7160</text></svg>
    <p class="stat-label">Hairdressers Booking</p>
  </div>
  <div class="stat" style="left:948px">
    <svg width="150" height="150" viewBox="0 0 150 150"><circle cx="75" cy="75" r="66" fill="none" stroke="#e6e6e6" stroke-width="9"/><circle cx="75" cy="75" r="66" fill="none" stroke="#abd036" stroke-width="9" stroke-dasharray="280 415" transform="rotate(-90 75 75)"/><text x="75" y="82" text-anchor="middle" font-family="Roboto, sans-serif" font-size="20" fill="#333">26 498</text></svg>
    <p class="stat-label">Reliable reviews</p>
  </div>
</section>

<section class="subscribe">
  <div class="subscribe-photo" role="img" aria-label="Soft photo of a woman with styled hair on a light background"></div>
  <h2>Nice TrimTable get tips? Subscribe!</h2>
  <div class="subscribe-form">
    <span>Wat is je emailadres?</span>
    <b><svg width="26" height="14" viewBox="0 0 26 14"><path d="M0 7h23M17 1l6 6-6 6" fill="none" stroke="#757575" stroke-width="2"/></svg></b>
  </div>
</section>

<footer class="footer">
  <div class="footer-col" style="left:88px">
    <h4>LINKS</h4>
    <ul><li>Customer Support</li><li>General Notes</li><li>Privacy Policy</li><li>Service Area</li><li>Site Index</li></ul>
  </div>
  <div class="footer-col" style="left:300px; width:300px">
    <h4>ABOUT US</h4>
    <p>We help you find and book a trusted hairdresser near you, any time of day.</p>
    <p style="margin-top:10px">Read reviews, compare prices and reserve your chair in just a few clicks.</p>
  </div>
  <div class="footer-col" style="left:652px; width:220px">
    <h4>GET IN TOUCH</h4>
    <p>Address: Keizerstraat 12, Amsterdam</p>
    <p style="margin-top:8px">Phone: +31 20 555 0142</p>
    <p style="margin-top:8px">Email: hello@trimtable.com</p>
  </div>
  <div class="footer-col" style="left:904px; width:260px">
    <h4>NEWSLETTER</h4>
    <p>Stay informed about new salons and special offers.</p>
    <div class="news-form"><span>Enter address</span><b>Submit</b></div>
    <div class="socials"><i></i><i></i><i></i></div>
  </div>
</footer>
<div class="copyright">Copyright © 2015 , All Rights Reserved</div>

</body>
</html>
```